Design concept for BrightKestrel.com Support Page

We are about to launch a new support page for our www.brightkestrel.com service for photographers and visual artists. The service provides media management, cloud storage, promotional and secure distribution to our members.

The support page will include FAQs and video tutorials.

In particular we're looking for a header for this page that suggests the user is in the support area of our service - so perhaps an illustration that suggests support could look nice (perhaps repair man or doctor iconography). Something to give this area of our site a different look and something that looks both cool and friendly.

Currently the page looks distinctly sparse and undesigned (see attached screenshot) - something that could be remedied, we feel, by some subtle design enhancements that we can implement using CSS.

```html
<!DOCTYPE html>
<html lang="en">
<head>
<meta charset="utf-8">
<title>BrightKestrel.com Support</title>
<link rel="stylesheet" href="https://fonts.googleapis.com/css2?family=Open+Sans:wght@400;600;700&display=swap">
<style>
  :root {
    --red: #d42b2b;
    --ink: #2e2e2e;
    --text: #6b6b6b;
    --muted: #9a9a9a;
    --rule: #dedede;
    --nav: #262626;
    --footer: #1c1c1c;
    --page: #ffffff;
  }
  * { box-sizing: border-box; margin: 0; padding: 0; }
  html, body { width: 831px; height: 1200px; overflow: hidden; }
  body { font-family: "Open Sans", Arial, sans-serif; background: var(--page); color: var(--text); position: relative; }
  .wrap { width: 743px; margin: 0 auto; }

  .site-header { height: 95px; position: relative; }
  .brand { position: absolute; left: 0; top: 24px; display: flex; align-items: center; gap: 8px; }
  .brand-mark { width: 26px; height: 26px; background: var(--ink); }
  .brand-name { font-size: 27px; font-weight: 700; color: var(--ink); letter-spacing: -0.5px; }
  .account { position: absolute; right: 0; top: 18px; display: flex; align-items: center; gap: 12px; font-size: 10px; font-weight: 700; }
  .account .login { color: var(--ink); }
  .account .signup { background: var(--red); color: #fff; padding: 4px 10px; }
  .search { position: absolute; right: 0; top: 52px; width: 150px; height: 20px; border: 1px solid var(--rule); font-size: 9px; color: var(--muted); padding: 3px 6px; display: flex; justify-content: space-between; align-items: center; }

  .main-nav { background: var(--nav); height: 26px; display: flex; padding-left: 12px; }
  .main-nav a { color: #fff; text-decoration: none; font-size: 10px; font-weight: 600; line-height: 26px; padding: 0 16px; letter-spacing: .3px; }
  .main-nav a.active { background: #3a3a3a; }

  .hero { position: relative; height: 206px; background: linear-gradient(180deg, #e9ecef 0%, #cfd6dc 45%, #b8ab93 75%, #8c7f6a 100%); }
  .hero-label { position: absolute; left: 0; top: 140px; background: var(--red); color: #fff; font-size: 14px; font-weight: 600; padding: 7px 20px 7px 14px; }

  .intro { padding-top: 16px; }
  .intro h1 { font-size: 21px; font-weight: 400; color: var(--ink); margin-bottom: 6px; }
  .intro p { font-size: 9.5px; line-height: 14px; width: 600px; }

  .section-title { font-size: 17px; font-weight: 400; color: var(--red); margin: 22px 0 10px; }
  .videos { display: flex; gap: 10px; }
  .video { width: 178px; }
  .video-thumb { height: 100px; position: relative; display: flex; align-items: center; justify-content: center; }
  .video-thumb.t1 { background: linear-gradient(135deg, #caa98b, #6e5646); }
  .video-thumb.t2 { background: linear-gradient(135deg, #6a6a6a, #2c2c2c); }
  .video-thumb.t3 { background: linear-gradient(135deg, #8c8c8c, #3f3f3f); }
  .video-thumb.t4 { background: linear-gradient(135deg, #c7a3d6, #7b4d9a); }
  .video h3 { font-size: 11px; font-weight: 600; color: var(--ink); margin: 6px 0 2px; }
  .video p { font-size: 8.5px; line-height: 12px; color: var(--muted); }

  .divider { height: 1px; background: var(--rule); margin-top: 26px; position: relative; }
  .divider::before { content: ""; position: absolute; left: 0; top: -1px; width: 70px; height: 3px; background: var(--red); }

  .faq-title { font-size: 17px; font-weight: 400; color: var(--ink); margin: 16px 0 10px; }
  .faq { border-bottom: 1px solid var(--rule); padding: 12px 0 16px; }
  .faq:last-of-type { border-bottom: 0; }
  .qa { display: flex; gap: 8px; font-size: 9px; line-height: 13.5px; }
  .qa + .qa { margin-top: 10px; }
  .qa b { color: var(--red); font-size: 11px; width: 14px; flex: none; }
  .qa.question span { color: var(--ink); }

  .site-footer { position: absolute; left: 0; bottom: 0; width: 831px; height: 98px; background: var(--footer); }
  .site-footer .wrap { position: relative; height: 100%; padding-top: 24px; }
  .footer-links { font-size: 10px; color: #fff; }
  .footer-links span { color: #777; margin: 0 4px; }
  .copyright { font-size: 8.5px; color: #888; margin-top: 6px; }
  .social { position: absolute; right: 0; top: 22px; display: flex; gap: 6px; }
  .social i { width: 16px; height: 16px; background: #3b7fc4; display: block; }
  .to-top { position: absolute; right: 0; bottom: 14px; font-size: 9px; color: #888; }
</style>
</head>
<body>
  <header class="site-header wrap">
    <div class="brand"><span class="brand-mark"></span><span class="brand-name">BrightKestrel</span></div>
    <div class="account"><span class="login">LOG IN</span><span class="signup">SIGN UP</span></div>
    <div class="search"><span>Search here</span>
      <svg width="9" height="9" viewBox="0 0 10 10"><circle cx="4" cy="4" r="3" fill="none" stroke="#999" stroke-width="1.3"/><line x1="6.3" y1="6.3" x2="9.3" y2="9.3" stroke="#999" stroke-width="1.3"/></svg>
    </div>
  </header>

  <nav class="main-nav wrap">
    <a class="active">HOME</a><a>GALLERIES</a><a>CONTRIBUTORS</a><a>PRICING</a><a>ARCHIVE</a><a>BLOG</a>
  </nav>

  <section class="hero wrap" role="img" aria-label="Photographer with camera and tripod on a sunny coastal path">
    <div class="hero-label">Bright Kestrel Support</div>
  </section>

  <main class="wrap">
    <section class="intro">
      <h1>Bright Kestrel Support</h1>
      <p>Bright Kestrel Support gathers answers, guides and short videos to help you manage, store, promote and share your work. Browse the tutorials below or scan the frequently asked questions to find a quick solution, and reach our team whenever you need a hand with your account.</p>
    </section>

    <h2 class="section-title">Video Tutorials</h2>
    <div class="videos">
      <article class="video">
        <div class="video-thumb t1" role="img" aria-label="Tutorial still of a smiling presenter">
          <svg width="30" height="30" viewBox="0 0 30 30"><circle cx="15" cy="15" r="14" fill="rgba(255,255,255,.85)"/><path d="M12 9l9 6-9 6z" fill="#333"/></svg>
        </div>
        <h3>Vivamus porttitor neque</h3>
        <p>Learn how to upload, tag and sort new images in a few minutes.</p>
      </article>
      <article class="video">
        <div class="video-thumb t2" role="img" aria-label="Tutorial still of camera equipment">
          <svg width="30" height="30" viewBox="0 0 30 30"><circle cx="15" cy="15" r="14" fill="rgba(255,255,255,.85)"/><path d="M12 9l9 6-9 6z" fill="#333"/></svg>
        </div>
        <h3>Vivamus porttitor neque</h3>
        <p>Set up cloud folders and keep every shoot backed up and safe.</p>
      </article>
      <article class="video">
        <div class="video-thumb t3" role="img" aria-label="Tutorial still of a camera lens close up">
          <svg width="30" height="30" viewBox="0 0 30 30"><circle cx="15" cy="15" r="14" fill="rgba(255,255,255,.85)"/><path d="M12 9l9 6-9 6z" fill="#333"/></svg>
        </div>
        <h3>Vivamus porttitor neque</h3>
        <p>Build a public portfolio page and promote your best collections.</p>
      </article>
      <article class="video">
        <div class="video-thumb t4" role="img" aria-label="Tutorial still of a portrait session">
          <svg width="30" height="30" viewBox="0 0 30 30"><circle cx="15" cy="15" r="14" fill="rgba(255,255,255,.85)"/><path d="M12 9l9 6-9 6z" fill="#333"/></svg>
        </div>
        <h3>Vivamus porttitor neque</h3>
        <p>Share private galleries with clients using secure delivery links.</p>
      </article>
    </div>

    <div class="divider"></div>

    <h2 class="faq-title">FAQ's</h2>
    <div class="faq">
      <p class="qa question"><b>Q:</b><span>How do I upload a large batch of images and keep the original file names and metadata intact when the upload finishes?</span></p>
      <p class="qa"><b>A:</b><span>Open the upload panel, drag your folder into the window and choose Keep metadata before you start. Files are processed in the background, so you can close the page while they finish. Once complete, every image keeps its name, caption and keywords, and you will find the batch in your Recent uploads folder ready to sort, tag and publish to your galleries. If a file fails, it is listed in the upload report so you can retry it with one click, and the rest of the batch stays in place.</span></p>
    </div>
    <div class="faq">
      <p class="qa question"><b>Q:</b><span>Can I control who sees my work and stop visitors from downloading full size files without permission?</span></p>
      <p class="qa"><b>A:</b><span>Yes. Each gallery has its own privacy setting, from public to invitation only. You can add watermarks, limit previews to web size and require a password for downloads. Client links can expire on a date you choose, and the activity log shows who viewed or saved each file so you always know where your images travel. Settings can be changed at any time and apply at once to every image inside the gallery you edit.</span></p>
    </div>
    <div class="faq">
      <p class="qa question"><b>Q:</b><span>How much storage comes with my plan and what happens when I reach the limit?</span></p>
      <p class="qa"><b>A:</b><span>Storage depends on your plan and is shown on your account page. When you near the limit we send a reminder, and you can upgrade at any time without losing files or links. Older archives can also be moved to cold storage to free space on your active plan.</span></p>
    </div>
  </main>

  <footer class="site-footer">
    <div class="wrap">
      <p class="footer-links">Home<span>|</span>Community Development<span>|</span>Affordable Housing<span>|</span>Alternative Energy<span>|</span>Crew Hub</p>
      <p class="copyright">© 2014 Company Name. All rights reserved. Terms of Use</p>
      <div class="social"><i></i><i></i><i></i></div>
      <span class="to-top">▲ Top</span>
    </div>
  </footer>
</body>
</html>
```